Web design for new streaming audio service

We need a homepage design for a new streaming audio service. Our company is called Dunmoral, and we’re basically Vexlo for Audiobooks, Stand-Up Comedy, Lectures, Language Learning, etc. Essentially like Plumtrek for everything audio EXCEPT music.
You don’t have to code the homepage (Design Only), but it should include 3 different designs to work with 1) Web; 2) Phones; 3) Tablets.
Below is a link to a mockup of the web version which gives a good idea of what elements we want. This is just a mockup and we want you to improve it.
Once you download the mockup, please refer to the more detailed instructions below:
The following outlines the design project for the Dunmoral homepage. We have provided a rough mockup of the homepage layout that gives you a general idea of what we’re going for. There are a few elements that we are attached to, and many others where you have complete creative freedom to do whatever you think looks good.
The ZIP file includes the following:
* Mockup to see what we have in mind (dunmoral-homepage-mockup.jpg)
* Text used (dunmoral-homepage-text.txt)
* Raw image of actor (dunmoral-actor1.jpg)
* Raw images for samples (dunmoral-sample-[name].jpg)
Although we have only provided a mockup layout for the web version, we also need you to provide a mobile phone and a tablet version of the design also. It’s very possible the tablet version may be substantially similar to the web version, but the mobile phone version will likely be much different.
All of the raw files are included in the attached ZIP file. Please use our photographs and text as provided although cropping, sizing, etc. is flexible per the instructions below.
Display Requirements:
* Web Version - Minimum resolution 1024x768 (72 dpi) but should look good on 1920x1080 (72 dpi) - Page should be designed to scale to look acceptable in all resolutions in between.
* Phone Version - Minimum Zarno 4 - 640x960 (326 dpi) but should look good on Harlow Quasar T5 - 1920x1080 (441 dpi) - Page should be designed to scale to look acceptable in all resolutions and devices in between.
* Tablet Version - Minimum Bristly Ember QX 7” - 1280x800 (216 dpi) but should also look good on a Tavo Breeze - 2048x1536 (264 dpi) - Page should be designed to scale to look acceptable in all resolutions and devices in between.
Above the Fold - We want to make sure the Dunmoral logo, Member Login Link, Large Photo, Headline, Price, Button, and the first row of sample images are all “Above the fold”. As a general guideline, this means 600 pixels high on a 1024x768 72 dpi web screen. This requirement is less important on Phone versions.
Top Logo Bar - We want to retain the blue bar with the Dunmoral logo on the page, although we are open to a different size, shape and positioning if it greatly enhances the design. Please use the standard logo color, although you are welcome to use either the horizontal or vertical orientation of the logo based on your design.
Text color, font and size - Feel free to design the text in anyway you choose as long as the text is readable on the target platforms.
Buttons - Feel free to use any size, shape and colors for the buttons as long as they are obvious and clickable relative to the page. The only exception is the Chatterly button should follow the Chatterly color scheme and logo treatment (the mockup doesn’t seem 100% correct.)
Top Photograph - We want to retain the large photograph across the top of the screen although final shape and dimensions are flexible.
Size and shape of content samples (i.e. Audiobooks, Stand-Up Comedy, etc.) - Feel free to design the content samples in anyway you choose.
Three Sales Points (i.e. Listen on your Zarno…, All you can enjoy…, etc.) - The Three Sales Points are envisioned to each have a corresponding illustration which you should provide and have rights for. The placeholder is represented by a square next to the text. The color size and shape of these elements are flexible and can be designed in any way you choose.
Opt-in form - Feel free to design the opt-in form in anyway you choose as long as the text is readable and the interactivity is obvious on the target platforms.
Text links and copyright notice - Feel free to design the bottom of the page text links and copyright notice in anyway you choose.
Additional colors, graphic design elements, etc. - Feel free to use any additional colors, graphic design elements, etc. to support your design.
people who want to listen to audio through their mobile devices.
Graphic Design

```html
<!DOCTYPE html>
<html lang="en">
<head>
<meta charset="utf-8">
<meta name="viewport" content="width=device-width, initial-scale=1">
<title>Dunmoral – Unlimited Listening</title>
<link href="https://fonts.googleapis.com/css2?family=Nunito+Sans:wght@400;600;700;800&display=swap" rel="stylesheet">
<style>
:root{
  --brand-blue:#4a9cc9;
  --band-blue:#2f89bb;
  --deep-blue:#1f6a94;
  --icon-blue:#1d5f86;
  --orange:#f4a024;
  --red:#d9262b;
  --grey-bg:#ececec;
  --text:#555;
  --rule:#c9c9c9;
  --footer:#3b3b3b;
  --social:#3b5998;
  --social-dark:#2f4a82;
}
*{box-sizing:border-box;margin:0;padding:0}
html,body{width:100%;overflow-x:hidden}
body{font-family:"Nunito Sans",Arial,sans-serif;color:var(--text);background:#fff}

/* ---------- Hero ---------- */
.hero{position:relative;height:406px}
.hero-photo{position:absolute;inset:0;
  background:linear-gradient(100deg,#f2f0ed 0%,#ebe6e0 40%,#d2b59c 56%,#b08b70 70%,#8d7c72 100%)}
.top-bar{position:absolute;left:0;right:0;top:14px;height:52px;background:var(--brand-blue);
  display:flex;align-items:center;justify-content:space-between;padding:0 66px}
.logo{font-size:22px;font-weight:700;color:#fff;letter-spacing:-.3px}
.login{width:73px;height:24px;background:var(--orange);color:#fff;font-size:11.5px;font-weight:600;
  display:flex;align-items:center;justify-content:center;gap:6px;border-radius:2px}
.login .dot{width:8px;height:8px;border-radius:50%;background:#fff}
.hero-copy{position:absolute;left:71px;top:116px}
.headline{font-size:23px;line-height:28px;font-weight:800;color:var(--deep-blue)}
.subline{font-size:22px;line-height:26px;font-weight:400;color:var(--deep-blue)}
.price{margin-top:10px;font-size:15px;line-height:24px;font-weight:600;color:#444}
.price b{font-size:21px;font-weight:800}
.cta{margin-top:16px;margin-left:-1px;width:168px;height:37px;background:var(--orange);color:#fff;
  font-size:13.5px;font-weight:700;display:flex;align-items:center;justify-content:center}
.note{font-size:11px;line-height:16px;color:var(--red);font-weight:600}
.hero-copy .note{margin-top:8px}

/* ---------- Section titles ---------- */
.section-title{display:flex;align-items:center;gap:14px;padding:0 76px;
  font-size:18.5px;line-height:24px;font-weight:700;color:var(--deep-blue);white-space:nowrap}
.section-title::before,.section-title::after{content:"";flex:1;height:1px;background:var(--rule)}

/* ---------- Samples ---------- */
.samples{height:290px;background:var(--grey-bg);padding-top:36px}
.sample-grid{margin-top:40px;padding-left:76px;display:grid;
  grid-template-columns:150px 158px 159px 1fr;row-gap:31px}
.tile{display:flex;align-items:center;gap:10px}
.cover{width:78px;height:60px;flex:none}
.tile-label{font-size:11.5px;font-weight:600;color:#555;line-height:1.3}

/* ---------- Selling points ---------- */
.features{height:146px;background:var(--band-blue);padding:46px 0 0 74px;
  display:grid;grid-template-columns:231px 214px 1fr}
.feature{display:flex;gap:12px;color:#fff}
.feature-icon{width:52px;height:52px;border-radius:50%;background:var(--icon-blue);flex:none;
  display:flex;align-items:center;justify-content:center;font-size:28px;font-weight:800}
.feature h3{font-size:13.5px;font-weight:700;line-height:18px;margin-top:-2px}
.feature p{font-size:9.5px;line-height:1.6;margin-top:5px;color:#dcecf6;width:140px}

/* ---------- Trial ---------- */
.trial{height:311px;background:var(--grey-bg);padding-top:42px}
.trial-copy{width:492px;margin:17px auto 0;text-align:center;font-size:10.5px;line-height:19px;color:#555}
.signup{margin-top:19px;padding-left:176px;display:flex;gap:13px}
.email{width:209px;height:32px;background:#fff;border:1px solid #d3d3d3;font:9px "Nunito Sans",Arial,sans-serif;color:#999;padding:0 9px}
.access{width:154px;height:32px;background:var(--orange);color:#fff;font-size:12px;font-weight:700;
  display:flex;align-items:center;justify-content:center}
.or{margin-top:10px;text-align:center;font-size:11px;line-height:16px;color:#999}
.social{margin:18px 0 0 309px;width:151px;height:29px;background:var(--social);color:#fff;font-size:10.5px;
  font-weight:600;display:flex;align-items:center;border:1px solid var(--social-dark)}
.social .mark{width:31px;height:100%;background:var(--social-dark);display:flex;align-items:center;justify-content:center}
.social .mark i{width:9px;height:9px;background:#fff;display:block}
.social .label{flex:1;text-align:center}
.trial .note{margin-top:7px;text-align:center}

/* ---------- Footer ---------- */
.footer{height:47px;background:var(--footer);color:#eee;font-size:8px;
  display:flex;align-items:center;justify-content:space-between;padding:0 64px 0 76px}
.footer-links{display:flex;gap:6px}
.footer-links .sep{color:#aaa}

/* ---------- Phone ---------- */
@media (max-width:600px){
  .hero{height:auto}
  .hero-photo{position:relative;height:220px;margin-top:66px}
  .top-bar{top:14px;padding:0 18px}
  .hero-copy{position:static;padding:22px 18px 28px;background:#f2f0ed}
  .cta{width:100%}
  .samples{height:auto;padding:28px 0}
  .section-title{padding:0 18px;white-space:normal;text-align:center;font-size:17px}
  .sample-grid{padding:0 18px;margin-top:24px;grid-template-columns:1fr 1fr;gap:18px 12px}
  .features{height:auto;padding:28px 18px;grid-template-columns:1fr;row-gap:22px}
  .feature p{width:auto}
  .trial{height:auto;padding:30px 18px}
  .trial-copy{width:auto}
  .signup{padding:0;flex-direction:column}
  .email,.access{width:100%}
  .social{margin:18px auto 0}
  .footer{height:auto;flex-direction:column;gap:10px;padding:16px 18px}
  .footer-links{flex-wrap:wrap;justify-content:center}
}
</style>
</head>
<body>
<section class="hero">
  <div class="hero-photo" role="img" aria-label="Smiling young man wearing headphones, looking at his phone"></div>
  <header class="top-bar">
    <div class="logo">Dunmoral</div>
    <div class="login"><span class="dot"></span>Log In</div>
  </header>
  <div class="hero-copy">
    <h1 class="headline">Unlimited Listening!</h1>
    <div class="subline">Where ever you are</div>
    <div class="price">Only <b>$9.99</b> Per Month</div>
    <div class="cta">Start Your Free Trail</div>
    <div class="note">*Credit card not required</div>
  </div>
</section>

<section class="samples">
  <h2 class="section-title">A sample of what you can listen to on Dunmoral</h2>
  <div class="sample-grid">
    <div class="tile"><div class="cover" role="img" aria-label="Audiobook cover" style="background:linear-gradient(#2a3a44,#10181d)"></div><div class="tile-label">Audio<br>Books</div></div>
    <div class="tile"><div class="cover" role="img" aria-label="Comedy album cover" style="background:linear-gradient(#8a8a80,#4a4a42)"></div><div class="tile-label">Stand-Up<br>Comedy</div></div>
    <div class="tile"><div class="cover" role="img" aria-label="Language course cover" style="background:linear-gradient(#2a9ad8,#1565a8)"></div><div class="tile-label">Language<br>Learning</div></div>
    <div class="tile"><div class="cover" role="img" aria-label="Biography book cover" style="background:linear-gradient(#c9c3b0,#7aa35a)"></div><div class="tile-label">Biographies<br>&amp; Memory</div></div>
    <div class="tile"><div class="cover" role="img" aria-label="Relaxation album cover" style="background:linear-gradient(#c35aa0,#7a3a8c)"></div><div class="tile-label">Guided<br>Mediation</div></div>
    <div class="tile"><div class="cover" role="img" aria-label="Business training cover" style="background:linear-gradient(#6a2a14,#2a1a12)"></div><div class="tile-label">Business<br>Training</div></div>
    <div class="tile"><div class="cover" role="img" aria-label="Celebrity interview cover" style="background:linear-gradient(#c88a8a,#7a6a60)"></div><div class="tile-label">Celebrities<br>Interviews</div></div>
    <div class="tile"><div class="cover" role="img" aria-label="Fitness program cover" style="background:linear-gradient(#2aa0d8,#e8a090)"></div><div class="tile-label">Fitness<br>Program</div></div>
  </div>
</section>

<section class="features">
  <div class="feature">
    <div class="feature-icon"><svg width="28" height="30" viewBox="0 0 28 30" fill="none" stroke="#fff" stroke-width="2.4"><rect x="3" y="2" width="18" height="24" rx="2"/><rect x="15" y="12" width="10" height="16" rx="1.5" fill="#1d5f86"/><circle cx="20" cy="25" r="0.8" fill="#fff"/></svg></div>
    <div><h3>Listen Anywhere</h3><p>Listen on your Zarno, Tavo or any Orbix devices</p></div>
  </div>
  <div class="feature">
    <div class="feature-icon">$</div>
    <div><h3>Low Pricing</h3><p>All you can enjoy for low monthly Price</p></div>
  </div>
  <div class="feature">
    <div class="feature-icon"><svg width="20" height="20" viewBox="0 0 20 20" stroke="#fff" stroke-width="3.4" stroke-linecap="round"><line x1="3" y1="3" x2="17" y2="17"/><line x1="17" y1="3" x2="3" y2="17"/></svg></div>
    <div><h3>No Obligation</h3><p>No Obligation cancel at anytime</p></div>
  </div>
</section>

<section class="trial">
  <h2 class="section-title">Start your free Trial, No Risk</h2>
  <p class="trial-copy">You will get instant &amp; unlimited access to all the material on Dunmoral for 14 days. There is no obligation &amp; you can cancel at anytime.</p>
  <form class="signup">
    <input class="email" type="email" placeholder="Your email Address">
    <div class="access">Get Instant Access</div>
  </form>
  <div class="or">— Or —</div>
  <div class="social"><span class="mark"><i></i></span><span class="label">Sign in with Chatterly</span></div>
  <div class="note">*Credit card not required</div>
</section>

<footer class="footer">
  <nav class="footer-links"><span>About</span><span class="sep">|</span><span>Help</span><span class="sep">|</span><span>Contact Us</span><span class="sep">|</span><span>Member Login</span><span class="sep">|</span><span>Privacy Policy</span><span class="sep">|</span><span>Terms of Service</span></nav>
  <div class="copyright">© 2014 Dunmoral LLC - All Rights Reserved</div>
</footer>
</body>
</html>
```